Letterhead Design for Law Firm

**Edit: I have added the photo of a bottom that I like.

------
We are looking for a re-design of our new letterhead. The letterhead is for a law firm and will be used for digital and traditionally printed correspondence.

Here are some suggestions:

- Please use colours are #8ec900 and simple black.
- Please do not use any type of "waves" at the bottom of the page. This is not in style at all.
- Please stay modern yet conservative.
- Please use font Segoe UI Light or similar if you can
- Avoid clipart or illustrations.
- Utilize ample white space in the layout so the design looks clean and information is easy to read at a glance. Don't overcrowd the letterhead.
- Make sure the letterhead design is consistent with our brand identity (see corvelith.ca)
-Please, no black headers or footers.

I am attaching my current letterhead and signature for your convenience.

Remember, the letterhead is an extension of our professional identity. We are a successful firm and trial lawyers who correspond with insurers, judges, lawyers, courts, clients, etc. Make it new, modern, attractive, yet powerful and conservative.

It needs to be easily printable. I would like the bleed removed in print so the black bar the bottom crosses the page (but the text is not near the edges)
Updates

Low design quality

Target Market(s)

Clients, Government Offices, Judiciary, Lawyers, Insurance Companies, Colleagues.

Industry/Entity Type

Law

Other font styles liked:
• Segoe UI LIght, Calibri Light,

Colors
00AB8E
00BBA5
67D7C9
C6EFE9
E9F9F6

Requirements
Must have
• Everything that is on the letterhead now.
Nice to have
• Cutting Edge design, yet conservative.
Should not have
• law firm cliche design, images,

```html
<!DOCTYPE html>
<html lang="en">
<head>
<meta charset="utf-8">
<title>Vernholt Personal Injury Lawyers — Letterhead</title>
<link href="https://fonts.googleapis.com/css2?family=Open+Sans:wght@300;400&display=swap" rel="stylesheet">
<style>
  :root {
    --brand-green: #8ec900;
    --ink: #111111;
    --bar-black: #000000;
    --paper: #ffffff;
    --backdrop: #c9c9c9;
  }
  html, body {
    margin: 0;
    padding: 0;
    width: 1200px;
    height: 686px;
    overflow: hidden;
    background: var(--backdrop);
  }
  .canvas {
    position: relative;
    width: 1200px;
    height: 686px;
  }
  .letterhead {
    position: absolute;
    left: 345px;
    top: 13px;
    width: 510px;
    height: 660px;
    background: var(--paper);
    font-family: "Open Sans", "Segoe UI", sans-serif;
    font-weight: 400;
    color: var(--ink);
    box-shadow: 0 6px 18px rgba(0,0,0,0.18);
  }
  .edge-bar {
    position: absolute;
    top: 0;
    bottom: 0;
    width: 8px;
  }
  .edge-bar--left { left: 0; background: var(--brand-green); }
  .edge-bar--right { right: 0; background: var(--bar-black); }

  .firm-name {
    position: absolute;
    left: 56px;
    top: 50px;
    font-size: 30px;
    font-weight: 400;
    letter-spacing: 1px;
    line-height: 1;
  }

  .contact-rule {
    position: absolute;
    left: 304px;
    top: 20px;
    width: 1px;
    height: 132px;
    background: var(--brand-green);
  }
  .contact {
    position: absolute;
    left: 314px;
    top: 22px;
    font-size: 7px;
    line-height: 10px;
    font-style: normal;
  }
  .contact p { margin: 0; }
  .contact .web-accent { color: var(--brand-green); }
  .contact .practice { margin-top: 8px; }

  .letter-body {
    position: absolute;
    left: 56px;
    top: 112px;
    width: 420px;
    font-size: 8px;
    line-height: 11px;
  }
  .letter-body p { margin: 0 0 8px; }
  .recipient { margin: 0 0 10px; }
  .recipient p { margin: 0; }

  .re-line {
    display: flex;
    align-items: flex-start;
  }
  .re-line .re-label {
    width: 60px;
    margin: 0;
  }
  .subject {
    font-size: 8.5px;
    line-height: 11px;
  }
  .subject p { margin: 0; }
  .subject-rule {
    margin: 10px 0 0 30px;
    width: 390px;
    height: 1px;
    background: var(--brand-green);
  }

  .sign-off {
    position: absolute;
    left: 230px;
    top: 486px;
    font-size: 8px;
    line-height: 11px;
  }
  .sign-off p { margin: 0; }
  .signature {
    display: block;
    margin: 6px 0;
    width: 150px;
    height: 42px;
    background: linear-gradient(90deg, #ececec, #f7f7f7);
  }
</style>
</head>
<body>
<div class="canvas">
  <article class="letterhead">
    <div class="edge-bar edge-bar--left"></div>
    <div class="edge-bar edge-bar--right"></div>

    <div class="firm-name">VERNHOLT</div>

    <div class="contact-rule"></div>
    <address class="contact">
      <p>www.<span class="web-accent">CORVELITH</span>.ca</p>
      <p>48 Harbour Street E., Suite 910</p>
      <p>Hamilton, ON&nbsp; L8R 2C6</p>
      <p>T: 905-555-0142</p>
      <p>F: 905-555-0187</p>
      <p>File Clerk: Mara Ellsworth</p>
      <p>Email: mara@corvelith.ca</p>
      <div class="practice">
        <p>Practice Restricted</p>
        <p>Serious Personal Injury</p>
        <p>Wrongful Death Litigation</p>
        <p>Long-Term Disability Litigation</p>
        <p>Wrongful Dismissal Litigation</p>
        <p>Employee Terminations</p>
      </div>
    </address>

    <section class="letter-body">
      <p>Without Prejudice</p>
      <p>March 13, 2024</p>
      <p>By Email</p>
      <div class="recipient">
        <p>Northgate Mutual Insurance</p>
        <p>Claims Litigation Department</p>
        <p>260 Fairview Road North</p>
        <p>P.O. Box 4100</p>
        <p>Waterloo, ON&nbsp;&nbsp;&nbsp;N2K 3B7</p>
      </div>
      <p>Attention:&nbsp; Mr. Colin Brandt</p>
      <p>Mr. Brandt:</p>
      <div class="re-line">
        <p class="re-label">Re:</p>
        <div class="subject">
          <p>Harrow v. Lindqvist et al.</p>
          <p>DOL:&nbsp; September 12, 2019</p>
          <p>Pre-Mediation Settlement Proposal – March 13th, 2024</p>
        </div>
      </div>
      <div class="subject-rule"></div>
    </section>

    <section class="sign-off">
      <p>Yours very truly,</p>
      <p>VERNHOLT PERSONAL INJURY LAWYERS</p>
      <span class="signature" role="img" aria-label="Handwritten signature of Daniel K. Vernholt"></span>
      <p>Daniel K. Vernholt</p>
      <p>Vernholt Law Professional Corporation</p>
      <p>/me</p>
      <p>Encl.</p>
    </section>
  </article>
</div>
</body>
</html>
```